Business cards and Stationary for engineering design firm
Brell Systems Advisory
Creative Brief
Professional
Dana Morrow
President
42 N 3rd St Emmaus, PA 18062
Dana@BrellSysAdvisory.com
www.BrellSysAdvisory.com
We are looking for modern and professional looking business cards for an engineering firm that specializes in the electric utility industry. Subtle touches like abstract poles and wires on the business cards are welcomed. Use your imagination and have fun!
We are up for anything. Maybe just the company logo and the website address for the back.

```html
<!DOCTYPE html>
<html lang="en">
<head>
<meta charset="utf-8">
<title>Brell Systems Advisory — Stationery</title>
<link rel="stylesheet" href="https://fonts.googleapis.com/css2?family=Lato:wght@400;700&display=swap">
<style>
  :root{
    --bg:#e6e8ea;
    --paper:#ffffff;
    --navy:#1f3a5c;
    --steel:#9aa6b4;
    --ink:#2a2f36;
    --muted:#7a828c;
    --flap-line:#dfe3e7;
    --env-back:#f7f8f9;
  }
  *{box-sizing:border-box;margin:0;padding:0}
  html,body{width:1200px;height:937px;overflow:hidden;background:var(--bg)}
  body{position:relative;font-family:'Lato',sans-serif;color:var(--ink)}
  .sheet{position:absolute;background:var(--paper);overflow:hidden;box-shadow:0 2px 6px rgba(0,0,0,.12)}
  .wave{position:absolute;left:0;bottom:0;width:100%;display:block}
  .wave-url{position:absolute;left:0;right:0;text-align:center;color:#fff;letter-spacing:2px;text-transform:uppercase;font-size:8px}

  .brand{display:flex;align-items:center;white-space:nowrap}
  .brand-mark{flex:none;background:var(--navy)}
  .brand-name{font-family:'Lato',sans-serif;font-weight:700;color:var(--navy);line-height:1}

  /* letterhead */
  .letterhead{left:182px;top:66px;width:388px;height:546px}
  .letterhead .brand{position:absolute;left:26px;top:28px;gap:7px}
  .letterhead .brand-mark{width:14px;height:14px}
  .letterhead .brand-name{font-size:13px}
  .lh-contact{position:absolute;right:24px;top:26px;text-align:right;font-size:5.5px;line-height:1.6;color:var(--muted)}
  .lh-body{position:absolute;left:26px;top:104px;width:330px;font-size:6px;line-height:1.55;color:var(--muted)}
  .lh-body p{margin-bottom:9px}
  .lh-sign{margin-top:22px}
  .letterhead .wave-url{bottom:10px}

  /* folder */
  .folder{left:633px;top:35px;width:519px;height:577px}
  .folder .brand{position:absolute;left:0;right:0;top:270px;justify-content:center;gap:14px}
  .folder .brand-mark{width:28px;height:28px}
  .folder .brand-name{font-size:30px}
  .folder .wave-url{bottom:14px;font-size:10px}

  /* business cards */
  .card{left:45px;width:198px}
  .card-front{top:658px;height:94px}
  .card-front .brand{position:absolute;left:10px;top:14px;gap:4px}
  .card-front .brand-mark{width:7px;height:7px}
  .card-front .brand-name{font-size:7.5px}
  .card-info{position:absolute;left:104px;top:12px;font-size:4.5px;line-height:1.6;color:var(--muted)}
  .card-info strong{color:var(--navy);font-size:5.5px}
  .card-back{top:772px;height:109px}
  .card-back .brand{position:absolute;left:0;right:0;top:48px;justify-content:center;gap:6px}
  .card-back .brand-mark{width:10px;height:10px}
  .card-back .brand-name{font-size:11px}

  /* envelope front */
  .envelope{left:266px;top:671px;width:430px;height:207px}
  .envelope .brand{position:absolute;left:18px;top:20px;gap:7px}
  .envelope .brand-mark{width:14px;height:14px}
  .envelope .brand-name{font-size:14px}
  .envelope .wave-url{bottom:12px;font-size:9px}

  /* envelope back */
  .envelope-back{left:734px;top:671px;width:426px;height:207px;background:var(--env-back)}
  .envelope-back .flap{position:absolute;left:0;top:0;width:100%;height:100%}
  .envelope-back .wave-url{top:22px;font-size:9px}
</style>
</head>
<body>

<svg width="0" height="0" style="position:absolute" aria-hidden="true">
  <defs>
    <symbol id="band" viewBox="0 0 400 60" preserveAspectRatio="none">
      <path d="M0,22 Q180,-4 400,10 L400,16 Q180,4 0,30Z" fill="var(--steel)"/>
      <path d="M0,30 Q180,6 400,16 L400,60 L0,60Z" fill="var(--navy)"/>
    </symbol>
  </defs>
</svg>

<section class="sheet letterhead">
  <div class="brand"><span class="brand-mark"></span><span class="brand-name">Brell Systems Advisory</span></div>
  <div class="lh-contact">
    42 N 3rd St Alderbrook, PA 18062<br>
    Dana@BrellSysAdvisory.com<br>
    www.BrellSysAdvisory.com
  </div>
  <div class="lh-body">
    <p>July 6, 2024</p>
    <p>Jane Doe<br>100 Main St, Alderbrook, PA</p>
    <p>Dear Client,</p>
    <p>Thank you for choosing our team for your upcoming utility design project. We review each line, pole and load with care so that every plan meets code and schedule.</p>
    <p>Our engineers will contact you this week to confirm site details and set a clear timeline for the first review.</p>
    <p>Please reach out with any questions at all.</p>
    <p>Sincerely,</p>
    <p class="lh-sign">Dana Morrow<br>President</p>
  </div>
  <svg class="wave" height="46"><use href="#band"/></svg>
  <div class="wave-url">www.BrellSysAdvisory.com</div>
</section>

<section class="sheet folder">
  <div class="brand"><span class="brand-mark"></span><span class="brand-name">Brell Systems Advisory</span></div>
  <svg class="wave" height="60"><use href="#band"/></svg>
  <div class="wave-url">www.BrellSysAdvisory.com</div>
</section>

<section class="sheet card card-front">
  <div class="brand"><span class="brand-mark"></span><span class="brand-name">Brell Systems Advisory</span></div>
  <div class="card-info">
    <strong>Dana Morrow</strong><br>
    President<br>
    42 N 3rd St Alderbrook, PA 18062<br>
    Dana@BrellSysAdvisory.com
  </div>
  <svg class="wave" height="22"><use href="#band"/></svg>
</section>

<section class="sheet card card-back">
  <div class="brand"><span class="brand-mark"></span><span class="brand-name">Brell Systems Advisory</span></div>
</section>

<section class="sheet envelope">
  <div class="brand"><span class="brand-mark"></span><span class="brand-name">Brell Systems Advisory</span></div>
  <svg class="wave" height="44"><use href="#band"/></svg>
  <div class="wave-url">www.BrellSysAdvisory.com</div>
</section>

<section class="sheet envelope-back">
  <svg class="flap" viewBox="0 0 426 207" preserveAspectRatio="none">
    <path d="M0,0 L426,0 L426,62 Q213,90 0,62Z" fill="var(--navy)"/>
    <path d="M0,62 Q213,90 426,62 L426,66 Q213,96 0,66Z" fill="var(--steel)"/>
    <path d="M0,207 L213,120 L426,207" fill="none" stroke="var(--flap-line)" stroke-width="1"/>
  </svg>
  <div class="wave-url">www.BrellSysAdvisory.com</div>
</section>

</body>
</html>
```